New Bicycle shop business card

Hi!
I'm looking for a business card for my new proffesional bike mechanics shop. This shop is only for fixing broken bikes and not selling bikes.
Peferbly a modern and sleek and modern design.
Colors: black, grey, red, white
Information:
Name: Rijwielwerkplaats Vanhoutte
Shop owner: Bart Vanhoutte & Marieke Segers
Website: www.rijwielwerkplaats-vanhoutte.be
Email: info@rijwielwerkplaats-vanhoutte.be
Phone number: +32471902368
Street adres: Kerkweg 46
9940 Bellebeke
Slogan/shop information: Herstellingen van alle merken.
Logo: see files.
Target Market(s)
People who seek a mechanic to fix or upgrade their bikes.
Contact Information for Business Card
Information:
Website: info@rijwielwerkplaats-vanhoutte.be
9940 Bellebeke
Logo: see files.

```html
<!DOCTYPE html>
<html lang="nl">
<head>
<meta charset="utf-8">
<title>Rijwielwerkplaats Vanhoutte – visitekaartje</title>
<link rel="stylesheet" href="https://fonts.googleapis.com/css2?family=Montserrat:wght@700&family=Lato:wght@400;700&display=swap">
<style>
  :root {
    --backdrop: #2a2a2a;
    --card: #151515;
    --card-edge: #222;
    --white: #f4f4f4;
    --grey: #c9c9c9;
    --rule: #4a4a4a;
    --red: #e0203f;
  }
  * { box-sizing: border-box; margin: 0; padding: 0; }
  html, body {
    width: 1200px; height: 900px; overflow: hidden;
    background: var(--backdrop);
  }
  .canvas {
    width: 1200px; height: 900px;
    display: flex; flex-direction: column; align-items: center; justify-content: center;
    gap: 40px;
  }
  .card {
    position: relative;
    width: 700px; height: 400px;
    border-radius: 22px;
    background: linear-gradient(160deg, #1d1d1d 0%, var(--card) 60%);
    border: 1px solid var(--card-edge);
    box-shadow: 0 14px 30px rgba(0,0,0,.45);
    overflow: hidden;
  }

  /* front side */
  .card-front { display: flex; flex-direction: column; align-items: center; justify-content: center; gap: 34px; }
  .brand {
    display: flex; align-items: center; gap: 14px;
    font-family: "Montserrat", sans-serif; font-weight: 700;
    color: var(--white); text-transform: uppercase; letter-spacing: .5px;
  }
  .brand-dot { width: 26px; height: 26px; border-radius: 50%; background: var(--red); flex: none; }
  .card-front .brand { font-size: 26px; }
  .slogan {
    font-family: "Montserrat", sans-serif; font-weight: 700;
    font-size: 15px; letter-spacing: .5px; color: var(--white);
    text-transform: uppercase;
  }

  /* back side */
  .card-back .brand {
    position: absolute; right: 40px; top: 70px;
    font-size: 22px;
  }
  .card-back .brand-dot { width: 20px; height: 20px; }
  .divider {
    position: absolute; left: 300px; right: 40px; top: 150px;
    height: 1px; background: var(--rule);
  }
  .address {
    position: absolute; right: 40px; top: 172px;
    font-family: "Lato", sans-serif; font-size: 17px; line-height: 1.35;
    color: var(--grey); text-align: right; font-style: normal;
  }
  .people { position: absolute; left: 40px; top: 228px; right: 40px; }
  .owners {
    display: flex; align-items: center; gap: 16px;
    font-family: "Lato", sans-serif; font-weight: 700; font-size: 17px;
    color: var(--red); text-transform: uppercase;
  }
  .owners::after { content: ""; flex: 1; height: 1px; background: var(--rule); }
  .role { font-family: "Lato", sans-serif; font-size: 16px; color: var(--grey); margin-top: 2px; }
  .contact { list-style: none; margin-top: 18px; }
  .contact li {
    display: flex; align-items: center; gap: 10px;
    font-family: "Lato", sans-serif; font-size: 16px; color: var(--grey);
    line-height: 1.7;
  }
  .contact svg { width: 15px; height: 15px; flex: none; }
</style>
</head>
<body>
<main class="canvas">

  <section class="card card-front" aria-label="Voorzijde">
    <div class="brand"><span class="brand-dot"></span>Rijwielwerkplaats Vanhoutte</div>
    <p class="slogan">Herstellingen van alle merken</p>
  </section>

  <section class="card card-back" aria-label="Achterzijde">
    <div class="brand"><span class="brand-dot"></span>Rijwielwerkplaats Vanhoutte</div>
    <div class="divider"></div>
    <address class="address">Kerkweg 46<br>9940 Bellebeke</address>

    <div class="people">
      <p class="owners">Bart Vanhoutte &amp; Marieke Segers</p>
      <p class="role">Owner</p>
      <ul class="contact">
        <li>
          <svg viewBox="0 0 16 16" aria-hidden="true"><path fill="#e0203f" d="M3.5 1.5l2.3 0 1 3-1.5 1.2a8 8 0 0 0 4.9 4.9l1.2-1.5 3 1v2.3c0 .8-.7 1.5-1.5 1.5A12.5 12.5 0 0 1 2 3c0-.8.7-1.5 1.5-1.5z"/></svg>
          +32471902368
        </li>
        <li>
          <svg viewBox="0 0 16 16" aria-hidden="true"><rect x="1" y="3" width="14" height="10" rx="1.2" fill="#e0203f"/><path d="M1.5 4l6.5 5 6.5-5" fill="none" stroke="#151515" stroke-width="1.4"/></svg>
          info@rijwielwerkplaats-vanhoutte.be
        </li>
        <li>
          <svg viewBox="0 0 16 16" aria-hidden="true"><circle cx="8" cy="8" r="7" fill="#e0203f"/><path d="M1 8h14M8 1c-3 3.5-3 10.5 0 14M8 1c3 3.5 3 10.5 0 14" fill="none" stroke="#151515" stroke-width="1.1"/></svg>
          www.rijwielwerkplaats-vanhoutte.be
        </li>
      </ul>
    </div>
  </section>

</main>
</body>
</html>
```